Revise our price listr for 2023

Please see attached price list with new prices to revise.
Please include new logo
Please add the text: Please note that prices are subject to change without prior notice.
Please remove prices from equipment with operator
Please add Under Commercial stone:
Fill Dirt $16.
Please add under Decorative Stone:
3/4" Barn Red Stone $127.
3/4" Yellow Ocean Gravel $140.
3/4" Delaware River Gravel $110.
1" Nutmeg Pebble $97.
Price list sending via email and customer in our lobby
Landscape and construction supply

```html
<!DOCTYPE html>
<html lang="en">
<head>
<meta charset="utf-8">
<title>2023 Material Price List</title>
<link href="https://fonts.googleapis.com/css2?family=Alfa+Slab+One&family=Poppins:wght@400;600;700&display=swap" rel="stylesheet">
<style>
  :root{
    --maroon:#6d1f22;
    --green:#1f9747;
    --ink:#3b3636;
    --paper:#ebe8e4;
    --paper-light:#f4f2ef;
    --page:#ffffff;
  }
  *{box-sizing:border-box;margin:0;padding:0}
  html,body{width:742px;height:1200px;overflow:hidden;background:var(--page)}
  body{position:relative;font-family:"Poppins",sans-serif;color:var(--ink)}
  .sheet{
    position:absolute;left:16px;top:348px;width:710px;height:503px;overflow:hidden;
    background:radial-gradient(ellipse at 30% 20%,var(--paper-light),var(--paper) 70%);
    box-shadow:0 4px 14px rgba(0,0,0,.18);
  }
  .abs{position:absolute}
  .brand{left:22px;top:30px;display:flex;align-items:center;gap:6px}
  .brand-dot{width:14px;height:14px;border-radius:50%;background:var(--green)}
  .brand-name{font-family:"Poppins",sans-serif;font-weight:700;color:var(--ink);font-size:12px;line-height:1;white-space:nowrap}
  .title-band{left:181px;top:25px;width:529px;height:45px;background:var(--maroon);border-radius:14px 0 0 14px;
    color:#fff;font-family:"Alfa Slab One",serif;font-size:31px;line-height:45px;padding-left:14px;letter-spacing:.2px;white-space:nowrap}
  .pill{background:var(--green);color:#fff;font-family:"Alfa Slab One",serif;text-align:center;border-radius:9px;
    font-size:13px;line-height:17px;height:17px}
  .list{font-size:5.6px;line-height:8.4px}
  .row{display:flex;align-items:flex-end}
  .row .lead{flex:1;border-bottom:.6px dotted currentColor;margin:0 3px 2px;opacity:.7}
  .row .price{color:var(--maroon);font-weight:700;width:18px}
  .on-dark{color:#fff}
  .on-dark .row .price{color:#fff}
  .sep{height:6px}
  .sep::before{content:"";position:absolute;left:10px;right:10px;top:2.5px;border-top:.6px solid var(--maroon);opacity:.6}
  .sep i{position:absolute;top:1px;width:3px;height:3px;border-radius:50%;background:var(--green)}
  .box{background:var(--maroon);border-radius:10px}
  .photo{border:1.5px solid var(--maroon);border-radius:8px}
  .eq-pill{left:503px;top:74px;width:178px;height:35px;font-size:12.5px;line-height:14px;padding-top:3px;border-radius:9px}
  .sub-head{color:var(--maroon);font-family:"Alfa Slab One",serif;font-size:9.5px;text-align:center;width:200px;left:492px}
  .eq-list{font-size:5.6px;line-height:8.2px}
  .note{font-size:5.4px;font-weight:700;line-height:7.5px;color:#222}
  .call{color:var(--maroon);font-weight:700}
  .know{left:492px;width:200px;text-align:center;color:var(--maroon);font-family:"Alfa Slab One",serif;font-size:13.5px}
  .know-text{left:497px;width:190px;text-align:center;color:var(--green);font-weight:700;font-size:5.6px;line-height:8px}
</style>
</head>
<body>
<main class="sheet">
  <div class="abs brand"><span class="brand-dot"></span><span class="brand-name">Fieldstone Yard Co.</span></div>
  <h1 class="abs title-band">2023 MATERIAL PRICE LIST</h1>

  <div class="abs pill" style="left:45px;top:82px;width:131px">SOIL</div>
  <div class="abs list" style="left:27px;top:104px;width:178px">
    <div class="row"><span>Sandy Loam</span><span class="lead"></span><span class="price">$30</span></div>
    <div class="row"><span>Topsoil-Screened</span><span class="lead"></span><span class="price">$42</span></div>
    <div class="row"><span>Garden Soil</span><span class="lead"></span><span class="price">$52</span></div>
    <div class="row"><span>Mushroom Dirt</span><span class="lead"></span><span class="price">$55</span></div>
    <div class="row"><span>Compost (Leaf &amp; Grass)</span><span class="lead"></span><span class="price">$55</span></div>
  </div>
  <div class="abs sep" style="left:27px;top:157px;width:180px"><i style="left:0"></i><i style="left:4px"></i><i style="right:4px"></i><i style="right:0"></i></div>

  <div class="abs pill" style="left:45px;top:172px;width:131px">MULCH</div>
  <div class="abs list" style="left:27px;top:194px;width:178px">
    <div class="row"><span>Mulch-Dyed Black</span><span class="lead"></span><span class="price">$42</span></div>
    <div class="row"><span>Mulch-Dyed Red</span><span class="lead"></span><span class="price">$42</span></div>
    <div class="row"><span>Mulch-Dyed Brown</span><span class="lead"></span><span class="price">$42</span></div>
    <div class="row"><span>Mulch-Natural Light Brown</span><span class="lead"></span><span class="price">$38</span></div>
    <div class="row"><span>Mulch-Dark Triple Ground</span><span class="lead"></span><span class="price">$44</span></div>
    <div class="row"><span>Mulch Cedar</span><span class="lead"></span><span class="price">$55</span></div>
  </div>
  <div class="abs sep" style="left:27px;top:259px;width:180px"><i style="left:0"></i><i style="left:4px"></i><i style="right:4px"></i><i style="right:0"></i></div>

  <div class="abs pill" style="left:34px;top:274px;width:165px">DECORATIVE STONE</div>
  <div class="abs list" style="left:27px;top:297px;width:178px">
    <div class="row"><span>White Limestone #1 [1/4"-1/2"]</span><span class="lead"></span><span class="price">$95</span></div>
    <div class="row"><span>White Limestone #2 [1/2"-3/4"]</span><span class="lead"></span><span class="price">$97.5</span></div>
    <div class="row"><span>River Rock #2 [3/4"] Round</span><span class="lead"></span><span class="price">$50</span></div>
    <div class="row"><span>River Rock-Medium [2/3"]</span><span class="lead"></span><span class="price">$95</span></div>
    <div class="row"><span>River Rounds [4-6"]</span><span class="lead"></span><span class="price">$90</span></div>
    <div class="row"><span>Pea Gravel</span><span class="lead"></span><span class="price">$50</span></div>
    <div class="row"><span>Berkshire Blend</span><span class="lead"></span><span class="price">$120</span></div>
    <div class="row"><span>3/4" Barn Red Stone</span><span class="lead"></span><span class="price">$127</span></div>
    <div class="row"><span>3/4" Yellow Ocean Gravel</span><span class="lead"></span><span class="price">$140</span></div>
    <div class="row"><span>3/4" Delaware River Gravel</span><span class="lead"></span><span class="price">$110</span></div>
    <div class="row"><span>1" Nutmeg Pebble</span><span class="lead"></span><span class="price">$97</span></div>
  </div>
  <div class="abs sep" style="left:27px;top:409px;width:180px"><i style="left:0"></i><i style="left:4px"></i><i style="right:4px"></i><i style="right:0"></i></div>

  <div class="abs pill" style="left:45px;top:426px;width:131px">SAND</div>
  <div class="abs list" style="left:27px;top:458px;width:178px">
    <div class="row"><span>Masonary/Pool Sand</span><span class="lead"></span><span class="price">$45</span></div>
    <div class="row"><span>Bedding Sand</span><span class="lead"></span><span class="price">$37</span></div>
  </div>

  <div class="abs box" style="left:248px;top:84px;width:213px;height:112px"></div>
  <div class="abs pill" style="left:264px;top:79px;width:165px">COMMERCIAL STONE</div>
  <div class="abs list on-dark" style="left:264px;top:103px;width:188px">
    <div class="row"><span>Item #4</span><span class="lead"></span><span class="price">$42</span></div>
    <div class="row"><span>#1 Stone (1/2")</span><span class="lead"></span><span class="price">$45</span></div>
    <div class="row"><span>#2 Stone (3/4" 1")</span><span class="lead"></span><span class="price">$45</span></div>
    <div class="row"><span>#3 (1.5" 2")</span><span class="lead"></span><span class="price">$45</span></div>
    <div class="row"><span>Stone Chip (fine)</span><span class="lead"></span><span class="price">$40</span></div>
    <div class="row"><span>Stone Dust (xtra fine)</span><span class="lead"></span><span class="price">$47</span></div>
    <div class="row"><span>Shale When Available</span><span class="lead"></span><span class="price">Call</span></div>
    <div class="row"><span>Bank Run Fill (Dirt &amp; Cobble)</span><span class="lead"></span><span class="price">$18</span></div>
    <div class="row"><span>Crusher Run</span><span class="lead"></span><span class="price">$42</span></div>
    <div class="row"><span>Fill Dirt</span><span class="lead"></span><span class="price">$16</span></div>
  </div>
  <div class="abs sep" style="left:252px;top:209px;width:205px"><i style="left:0"></i><i style="left:4px"></i><i style="right:4px"></i><i style="right:0"></i></div>

  <div class="abs pill" style="left:292px;top:221px;width:131px">SEASONAL</div>
  <div class="abs list" style="left:264px;top:246px;width:188px">
    <div class="row"><span>Treated Salt Green</span><span class="lead"></span><span class="price">$145</span></div>
  </div>
  <div class="abs sep" style="left:252px;top:266px;width:205px"><i style="left:0"></i><i style="left:4px"></i><i style="right:4px"></i><i style="right:0"></i></div>

  <div class="abs box" style="left:248px;top:288px;width:213px;height:72px"></div>
  <div class="abs pill" style="left:264px;top:283px;width:165px">DELIVERY CHARGES</div>
  <div class="abs list on-dark" style="left:264px;top:306px;width:188px">
    <div class="row"><span>Local (Small Truck)</span><span class="lead"></span><span class="price">$60</span></div>
    <div class="row"><span>Local (Medium Truck)</span><span class="lead"></span><span class="price">475</span></div>
    <div class="row"><span>Local (Large Truck)</span><span class="lead"></span><span class="price">$115</span></div>
    <div style="font-weight:700;text-align:center;font-size:5.4px">Local Delivering 7 Mile Radius Excluding the Mat</div>
    <div style="font-weight:700;text-align:right;font-size:5.6px;padding-right:6px">CALL FOR QUOTE</div>
  </div>
  <div class="abs sep" style="left:252px;top:373px;width:205px"><i style="left:0"></i><i style="left:4px"></i><i style="right:4px"></i><i style="right:0"></i></div>

  <div class="abs photo" role="img" aria-label="Hands holding dark garden soil" style="left:246px;top:389px;width:107px;height:91px;background:radial-gradient(circle at 55% 60%,#6b4b3a,#1d1a18 70%)"></div>
  <div class="abs photo" role="img" aria-label="Rippled beige sand" style="left:357px;top:389px;width:105px;height:91px;background:linear-gradient(135deg,#e4cdae,#c9a987)"></div>

  <div class="abs pill eq-pill">EQUIPMENT WITH<br>OPERATOR AVAILABLE</div>
  <div class="abs sub-head" style="top:112px">CALL FOR PRICING</div>
  <div class="abs eq-list" style="left:501px;top:128px">Onsite Mobile<br>Grinding/Tub Grinding<br>Forestry Mulching</div>
  <div class="abs eq-list" style="left:501px;top:156px">Skid Steer : (Rubber Track)<br>Available Attachment<br>Power Rake<br>Forestry Mulching</div>
  <div class="abs eq-list" style="left:636px;top:164px">3/4 Yard Bucket<br>Hydraulic Auger<br>Grapple Bucket</div>
  <div class="abs sub-head" style="top:201px">EXCAVATOR</div>
  <div class="abs eq-list" style="left:501px;top:225px">35 Class (7,500lbs)<br>60 Class (14,000lbs)<br>140 Class (45,500lbs)<br>160 Class (38,500lbs)<br>250 Class (60,000lbs)</div>
  <div class="abs sub-head" style="top:276px">BULL DOZER</div>
  <div class="abs eq-list" style="left:501px;top:300px">450 Class (18,000lbs)<br>700 Class (30,000lbs)<br>Vibratory Roller<br>Rock Hammer</div>
  <div class="abs note" style="left:501px;top:340px;width:185px">Hydraulic Rock Hammer on 160 Class excavator. Additional mobilization fee for 1st day day</div>
  <div class="abs list" style="left:501px;top:362px;width:185px">
    <div class="row"><span>Tri-Axle Dump</span><span class="lead"></span><span class="call">Call</span></div>
    <div class="row"><span>Dump Trailer</span><span class="lead"></span><span class="call">Call</span></div>
  </div>
  <div class="abs know" style="top:387px">DID YOU KNOW?</div>
  <div class="abs know-text" style="top:405px">We Offer Onside Tub Grinding &amp; We are a GREEN RECYCLING Location! NON LOCAL CALL FOR PRICING ALSO THANK YOU</div>
  <div class="abs" role="img" aria-label="Pile of smooth river pebbles" style="left:502px;top:432px;width:208px;height:71px;background:linear-gradient(180deg,rgba(235,232,228,0),#a89a88 35%,#5d5349)"></div>
</main>
</body>
</html>
```